Networking Events Calendar/Diary

We need a responsive website that can act as both an online diary/calendar and a resource for community and networking events similar to brimtolvenquarrix.com (we do not want a clone, but one with similar functionality). We need to be able to host adverts, have a client area for clients to add their own events to the diary. This needs to have the functionality that clients have to pay to add recurring events. Some integration would be useful so that if a clients already has their own online diary on their website then using an API possibly to also add that event into our online diary

Industry/Entity Type

Events

Coding

Coded - Design and coding required

Number of Pages Required

5+ page

Requirements
Must have
• My project must have a calendar area, space for ads, be responsive and easily viewable on mobile. A subscribers area for clients and a way to purchase premium status so that premium events are highlighted.

```html
<!DOCTYPE html>
<html lang="en">
<head>
<meta charset="utf-8">
<title>Kelvor Events – Networking Events Diary</title>
<link href="https://fonts.googleapis.com/css2?family=Oswald:wght@400;500&family=Roboto:wght@400;500;700&display=swap" rel="stylesheet">
<style>
  :root{
    --blue:#3ea3dc;
    --blue-dark:#1f86c0;
    --ink:#1e1e1e;
    --text:#444;
    --muted:#777;
    --page:#ececec;
    --card:#ffffff;
    --line:#dcdcdc;
    --night:#161616;
    --btn-dark:#4a4f55;
  }
  *{box-sizing:border-box;margin:0;padding:0}
  html,body{width:1200px;height:2387px;overflow:hidden}
  body{position:relative;background:var(--page);font-family:"Roboto",Arial,sans-serif;color:var(--text)}
  a{color:inherit;text-decoration:none}

  /* header */
  .site-header{position:absolute;left:0;top:0;width:1200px;height:121px;background:#fff;box-shadow:0 2px 6px rgba(0,0,0,.12);z-index:2}
  .brand{position:absolute;left:84px;top:46px;font-family:"Roboto",Arial,sans-serif;font-weight:500;font-size:30px;letter-spacing:2px;color:var(--ink)}
  .main-nav{position:absolute;left:489px;top:56px;display:flex;gap:0}
  .main-nav a{font-size:14px;color:var(--ink);margin-right:0}
  .main-nav a.active{color:var(--blue)}
  .nav-home{position:absolute;left:0}
  .login{position:absolute;left:1044px;top:51px;width:67px;height:25px;background:var(--blue);color:#fff;font-size:11px;font-weight:500;display:flex;align-items:center;justify-content:center;border-radius:2px}

  /* hero */
  .hero{position:absolute;left:0;top:121px;width:1200px;height:598px;overflow:hidden}
  .hero-photo{position:absolute;inset:0;background:linear-gradient(100deg,#f4f8fb 0%,#dde9f2 35%,#b9cfe0 55%,#6f8fab 75%,#2f4a66 100%)}
  .hero-title{position:absolute;left:86px;top:292px;font-family:"Oswald",Arial,sans-serif;font-weight:400;font-size:38px;color:#1b1b1b;letter-spacing:.3px}
  .hero-sub{position:absolute;left:86px;top:341px;font-family:"Oswald",Arial,sans-serif;font-weight:400;font-size:47px;color:var(--blue);letter-spacing:.3px}
  .hero-arrows{position:absolute;left:84px;top:520px;display:flex;gap:2px}
  .hero-arrows span{width:31px;height:32px;background:#3b3f44;display:flex;align-items:center;justify-content:center}

  /* blog */
  .section-title{position:absolute;left:86px;top:772px;font-size:19px;font-weight:400;color:var(--ink)}
  .section-title em{font-style:normal;color:var(--blue)}
  .post{position:absolute;left:86px;width:718px;height:239px;background:var(--card);border:1px solid var(--line);box-shadow:0 1px 3px rgba(0,0,0,.08)}
  .post-photo{position:absolute;left:13px;top:13px;width:238px;height:201px;border:4px solid #fff;box-shadow:0 0 0 1px var(--line)}
  .post-body{position:absolute;left:275px;top:30px;width:420px}
  .post-title{font-size:16px;font-weight:400;color:var(--blue);margin-bottom:8px}
  .post-meta{font-size:14px;color:var(--ink);margin-bottom:17px;word-spacing:1px}
  .post-excerpt{font-size:12.6px;line-height:21px;color:var(--muted);text-align:justify}
  .post-actions{position:absolute;left:275px;top:178px;display:flex;align-items:center;gap:14px}
  .btn-more{width:92px;height:28px;background:var(--blue);color:#fff;font-size:11px;font-weight:700;display:flex;align-items:center;justify-content:center;border-radius:2px}
  .share{display:flex;align-items:center;gap:3px;font-size:9px;color:#555}
  .share b{height:17px;padding:0 5px;border:1px solid #ccc;border-radius:2px;display:flex;align-items:center;font-weight:500;background:#f6f6f6}
  .share i{height:17px;min-width:16px;border:1px solid #ccc;font-style:normal;display:flex;align-items:center;justify-content:center;background:#fff}

  /* sidebar */
  .widget{position:absolute;left:823px;width:286px;background:var(--card);border:1px solid var(--line);box-shadow:0 1px 3px rgba(0,0,0,.08)}
  .widget-head{height:41px;background:var(--blue);color:#fff;display:flex;align-items:center;padding-left:25px}
  .events-widget{top:815px;height:500px}
  .events-widget .widget-head{font-size:15px;font-weight:500}
  .event-item{display:flex;gap:11px;padding:11px 0 10px 23px;margin-right:26px;border-bottom:1px solid #eee;height:88px}
  .event-thumb{width:80px;height:56px;flex:none;border:3px solid #fff;box-shadow:0 0 0 1px var(--line);margin-top:6px}
  .event-text h4{font-size:12px;font-weight:400;color:var(--blue-dark);margin-bottom:2px}
  .event-text p{font-size:10.5px;line-height:16px;color:var(--muted)}
  .archives{top:1330px;height:254px}
  .archives .widget-head{font-size:19px;font-weight:500;padding-left:32px}
  .archive-list{list-style:none;padding:14px 0 0 32px}
  .archive-list li{display:flex;align-items:center;gap:10px;font-size:14px;color:var(--text);height:35px}
  .video{position:absolute;left:823px;top:1596px;width:287px;height:214px;border:1px solid var(--line);background:linear-gradient(135deg,#e9eef2 0%,#c9d3db 50%,#8d9aa6 100%)}
  .play{position:absolute;left:115px;top:78px}

  /* pagination */
  .pager{position:absolute;left:88px;top:1833px;display:flex;gap:10px}
  .pager span{height:26px;min-width:25px;padding:0 6px;background:var(--btn-dark);color:#fff;font-size:12px;font-weight:500;display:flex;align-items:center;justify-content:center;border-radius:2px}
  .pager span.wide{width:51px}
  .pager span.current{background:var(--blue)}

  /* advert */
  .advert{position:absolute;left:86px;top:1927px;width:1022px;height:128px;background:linear-gradient(180deg,#3a0505 0%,#b3120f 55%,#5a0707 100%);overflow:hidden}
  .advert-line{position:absolute;left:27px;top:18px;font-family:"Oswald",Arial,sans-serif;font-weight:500;font-size:27px;color:#fff;letter-spacing:.8px}
  .advert-brand{position:absolute;right:26px;top:22px;width:250px;height:70px;background:#e8e8e4;display:flex;align-items:center;justify-content:center;font-family:"Oswald",Arial,sans-serif;font-weight:500;font-size:38px;color:#3d3d3d}
  .advert-note{position:absolute;right:26px;top:100px;font-family:"Oswald",Arial,sans-serif;font-size:15px;color:#fff}

  /* footer */
  .site-footer{position:absolute;left:0;top:2094px;width:1200px;height:225px;background:var(--blue-dark);color:#fff}
  .foot-col{position:absolute;top:45px}
  .foot-col h5{font-size:15px;font-weight:500;letter-spacing:.4px;margin-bottom:21px}
  .foot-col p{font-size:11px;line-height:17px;color:#e6f2fa}
  .about{left:86px;width:234px}
  .about p+p{margin-top:17px}
  .links{left:433px}
  .links ul{list-style:none}
  .links li{font-size:11px;height:24px;color:#e6f2fa;display:flex;align-items:center;gap:6px}
  .contact{left:649px;width:200px}
  .contact p{margin-bottom:13px}
  .newsletter{left:906px;width:204px}
  .signup{display:flex;margin-top:13px}
  .signup span{width:141px;height:30px;background:#fff;color:#777;font-size:10px;display:flex;align-items:center;padding-left:13px}
  .signup b{width:62px;height:30px;background:#151515;font-size:10px;font-weight:500;display:flex;align-items:center;justify-content:center}
  .social{display:flex;gap:15px;margin-top:14px}
  .social span{width:31px;height:31px;border:1px solid #fff;border-radius:50%}
  .bottom-bar{position:absolute;left:0;top:2319px;width:1200px;height:68px;background:var(--night);color:#fff;font-size:12px;display:flex;align-items:center;justify-content:center}
</style>
</head>
<body>

<header class="site-header">
  <div class="brand">KELVOR EVENTS</div>
  <nav class="main-nav">
    <a class="active" href="#" style="position:absolute;left:0">HOME</a>
    <a href="#" style="position:absolute;left:73px;white-space:nowrap">ABOUT US</a>
    <a href="#" style="position:absolute;left:171px">SERVICES</a>
    <a href="#" style="position:absolute;left:269px;white-space:nowrap">ONLINE DIARY</a>
    <a href="#" style="position:absolute;left:391px">BLOG</a>
    <a href="#" style="position:absolute;left:463px">CONTACTS</a>
  </nav>
  <a class="login" href="#">LOG IN</a>
</header>

<section class="hero">
  <div class="hero-photo" role="img" aria-label="Business team at a laptop giving thumbs up in a bright office"></div>
  <h1 class="hero-title">NEQUE PORRO QUISQUAM</h1>
  <h2 class="hero-sub">NETWORKING EVENTS</h2>
  <div class="hero-arrows">
    <span><svg width="10" height="16" viewBox="0 0 10 16"><path d="M8 1 2 8l6 7" fill="none" stroke="#fff" stroke-width="1.6"/></svg></span>
    <span><svg width="10" height="16" viewBox="0 0 10 16"><path d="M2 1l6 7-6 7" fill="none" stroke="#fff" stroke-width="1.6"/></svg></span>
  </div>
</section>

<h3 class="section-title">LATEST <em>BLOG</em></h3>

<article class="post" style="top:813px">
  <div class="post-photo" role="img" aria-label="Laptop with a calendar on screen on a wooden desk" style="background:linear-gradient(135deg,#5a4636,#a8927a 55%,#3e3a38)"></div>
  <div class="post-body">
    <h4 class="post-title">Neque porro quisquam est qui dolorem ipsum</h4>
    <p class="post-meta">Post by : admin &nbsp;&nbsp;| &nbsp;&nbsp;Post on : October 1, 2015 &nbsp;at &nbsp;10.15 a.m</p>
    <p class="post-excerpt">Sed id tincidunt arcu. Maecenas eget elit at purus dapibus dictum. Vestibulum ante ipsum primis in faucibus orci luctus et ultrices posuere cubilia Curae; In hac habitasse platea dictumst.</p>
  </div>
  <div class="post-actions">
    <a class="btn-more" href="#">LEARN MORE</a>
    <div class="share"><b>Post</b><i>0</i></div>
    <div class="share"><b>Like</b><i>0</i></div>
    <div class="share"><b>+1</b><i>0</i></div>
  </div>
</article>

<article class="post" style="top:1063px">
  <div class="post-photo" role="img" aria-label="Colleagues talking around a meeting table" style="background:linear-gradient(135deg,#e9e4de,#b89c86 50%,#5b4a42)"></div>
  <div class="post-body">
    <h4 class="post-title">Neque porro quisquam est qui dolorem ipsum</h4>
    <p class="post-meta">Post by : admin &nbsp;&nbsp;| &nbsp;&nbsp;Post on : October 1, 2015 &nbsp;at &nbsp;10.15 a.m</p>
    <p class="post-excerpt">Sed id tincidunt arcu. Maecenas eget elit at purus dapibus dictum. Vestibulum ante ipsum primis in faucibus orci luctus et ultrices posuere cubilia Curae; In hac habitasse platea dictumst.</p>
  </div>
  <div class="post-actions">
    <a class="btn-more" href="#">LEARN MORE</a>
    <div class="share"><b>Post</b><i>0</i></div>
    <div class="share"><b>Like</b><i>0</i></div>
    <div class="share"><b>+1</b><i>0</i></div>
  </div>
</article>

<article class="post" style="top:1316px">
  <div class="post-photo" role="img" aria-label="Business people seated in a bright lounge" style="background:linear-gradient(135deg,#f1f3f4,#b9c2c9 50%,#3f464e)"></div>
  <div class="post-body">
    <h4 class="post-title">Neque porro quisquam est qui dolorem ipsum</h4>
    <p class="post-meta">Post by : admin &nbsp;&nbsp;| &nbsp;&nbsp;Post on : October 1, 2015 &nbsp;at &nbsp;10.15 a.m</p>
    <p class="post-excerpt">Sed id tincidunt arcu. Maecenas eget elit at purus dapibus dictum. Vestibulum ante ipsum primis in faucibus orci luctus et ultrices posuere cubilia Curae; In hac habitasse platea dictumst.</p>
  </div>
  <div class="post-actions">
    <a class="btn-more" href="#">LEARN MORE</a>
    <div class="share"><b>Post</b><i>0</i></div>
    <div class="share"><b>Like</b><i>0</i></div>
    <div class="share"><b>+1</b><i>0</i></div>
  </div>
</article>

<article class="post" style="top:1571px">
  <div class="post-photo" role="img" aria-label="Team reviewing charts on a table" style="background:linear-gradient(135deg,#2e3440,#8b96a3 45%,#eef2f5)"></div>
  <div class="post-body">
    <h4 class="post-title">Neque porro quisquam est qui dolorem ipsum</h4>
    <p class="post-meta">Post by : admin &nbsp;&nbsp;| &nbsp;&nbsp;Post on : October 1, 2015 &nbsp;at &nbsp;10.15 a.m</p>
    <p class="post-excerpt">Sed id tincidunt arcu. Maecenas eget elit at purus dapibus dictum. Vestibulum ante ipsum primis in faucibus orci luctus et ultrices posuere cubilia Curae; In hac habitasse platea dictumst.</p>
  </div>
  <div class="post-actions">
    <a class="btn-more" href="#">LEARN MORE</a>
    <div class="share"><b>Post</b><i>0</i></div>
    <div class="share"><b>Like</b><i>0</i></div>
    <div class="share"><b>+1</b><i>0</i></div>
  </div>
</article>

<aside class="widget events-widget">
  <div class="widget-head">NETWORKING EVENTS</div>
  <div class="event-item"><div class="event-thumb" role="img" aria-label="Conference hall" style="background:linear-gradient(135deg,#d7e1ea,#7b8fa3)"></div><div class="event-text"><h4>This is a sample Post 1</h4><p>Lorem ipsum dolor sit amet, consectetuer adipiscing elit, sed diam nonummy nibh...</p></div></div>
  <div class="event-item"><div class="event-thumb" role="img" aria-label="Business meeting" style="background:linear-gradient(135deg,#e8e2da,#8c7767)"></div><div class="event-text"><h4>This is a sample Post 1</h4><p>Lorem ipsum dolor sit amet, consectetuer adipiscing elit, sed diam nonummy nibh...</p></div></div>
  <div class="event-item"><div class="event-thumb" role="img" aria-label="City skyline" style="background:linear-gradient(180deg,#eef1f3,#9aa4ab)"></div><div class="event-text"><h4>This is a sample Post 1</h4><p>Lorem ipsum dolor sit amet, consectetuer adipiscing elit, sed diam nonummy nibh...</p></div></div>
  <div class="event-item"><div class="event-thumb" role="img" aria-label="Team group" style="background:linear-gradient(135deg,#f0ece8,#6d7d8c)"></div><div class="event-text"><h4>This is a sample Post 1</h4><p>Lorem ipsum dolor sit amet, consectetuer adipiscing elit, sed diam nonummy nibh...</p></div></div>
  <div class="event-item" style="border-bottom:0"><div class="event-thumb" role="img" aria-label="Colleagues at a desk" style="background:linear-gradient(135deg,#e3e7ea,#4f5863)"></div><div class="event-text"><h4>This is a sample Post 1</h4><p>Lorem ipsum dolor sit amet, consectetuer adipiscing elit, sed diam nonummy nibh...</p></div></div>
</aside>

<aside class="widget archives">
  <div class="widget-head">ARCHIVES</div>
  <ul class="archive-list">
    <li><svg width="12" height="10" viewBox="0 0 12 10"><path d="M1 1l4 4-4 4M6 1l4 4-4 4" fill="none" stroke="#3ea3dc" stroke-width="1.5"/></svg>April 2015</li>
    <li><svg width="12" height="10" viewBox="0 0 12 10"><path d="M1 1l4 4-4 4M6 1l4 4-4 4" fill="none" stroke="#3ea3dc" stroke-width="1.5"/></svg>March 2015</li>
    <li><svg width="12" height="10" viewBox="0 0 12 10"><path d="M1 1l4 4-4 4M6 1l4 4-4 4" fill="none" stroke="#3ea3dc" stroke-width="1.5"/></svg>February 2015</li>
    <li><svg width="12" height="10" viewBox="0 0 12 10"><path d="M1 1l4 4-4 4M6 1l4 4-4 4" fill="none" stroke="#3ea3dc" stroke-width="1.5"/></svg>January 2015</li>
    <li><svg width="12" height="10" viewBox="0 0 12 10"><path d="M1 1l4 4-4 4M6 1l4 4-4 4" fill="none" stroke="#3ea3dc" stroke-width="1.5"/></svg>September 2014</li>
  </ul>
</aside>

<div class="video" role="img" aria-label="Video of business people walking through a glass corridor">
  <svg class="play" width="58" height="58" viewBox="0 0 58 58"><circle cx="29" cy="29" r="28" fill="rgba(30,30,30,.65)"/><path d="M23 18v22l18-11z" fill="#fff"/></svg>
</div>

<nav class="pager">
  <span class="wide">Prev</span>
  <span class="current">1</span>
  <span>2</span><span>3</span><span>4</span><span>5</span><span>6</span>
  <span>…</span><span>22</span>
  <span class="wide">Next</span>
</nav>

<div class="advert" role="img" aria-label="Advert banner with a concert crowd: Reach 9 million unique users, advertise on Quellnet">
  <p class="advert-line">REACH 9 MILLION UNIQUE USERS &nbsp;•&nbsp; ADVERTISE ON QUELLNET</p>
  <div class="advert-brand">Quellnet</div>
  <p class="advert-note">Powered by VARNISTO</p>
</div>

<footer class="site-footer">
  <div class="foot-col about">
    <h5>TEXT WIDGET</h5>
    <p>Tandria helps you to quickly and easily build incredible websites with Plumeframe.</p>
    <p>Proin gravida nibh vel velit auctor aliquet. Aenean sollicitudin, lorem quis bibendum auctor, nisi elit consequat ipsum, nec sagittis.</p>
  </div>
  <div class="foot-col links">
    <h5>LINKS</h5>
    <ul>
      <li><svg width="5" height="8" viewBox="0 0 5 8"><path d="M0 0l5 4-5 4z" fill="#fff"/></svg>Customer Support</li>
      <li><svg width="5" height="8" viewBox="0 0 5 8"><path d="M0 0l5 4-5 4z" fill="#fff"/></svg>Documentation</li>
      <li><svg width="5" height="8" viewBox="0 0 5 8"><path d="M0 0l5 4-5 4z" fill="#fff"/></svg>Resources</li>
      <li><svg width="5" height="8" viewBox="0 0 5 8"><path d="M0 0l5 4-5 4z" fill="#fff"/></svg>General FAQs</li>
      <li><svg width="5" height="8" viewBox="0 0 5 8"><path d="M0 0l5 4-5 4z" fill="#fff"/></svg>Shortcodes</li>
    </ul>
  </div>
  <div class="foot-col contact">
    <h5>GET IN TOUCH</h5>
    <p>Address : 1420 Orrin Lane,<br>Pelbrook, NJ</p>
    <p>Phone : 201 555 0148</p>
    <p>Email : info@kelvorevents.com</p>
  </div>
  <div class="foot-col newsletter">
    <h5>NEWSLETTER</h5>
    <p>Your about us information would fit here nicely.</p>
    <div class="signup"><span>Email address</span><b>SUBMIT</b></div>
    <div class="social"><span></span><span></span><span></span></div>
  </div>
</footer>

<div class="bottom-bar">Copyright © 2015. All Rights Reserved</div>

</body>
</html>
```